Brellwick Partners, LLC Stationary

Brellwick Partners, LLC is a new financial planning and consulting company. We are looking for designs on business cards, letterhead, envelopes, and anything else that would be useful. Our preference for business card design is two sided. We are looking for a professional and clean look with incorporating the logo and patriotic feel. Thank you to all who participate and good luck!

```html
<!DOCTYPE html>
<html lang="en">
<head>
<meta charset="utf-8">
<title>Brellwick Partners, LLC – Business Card</title>
<link rel="stylesheet" href="https://fonts.googleapis.com/css2?family=Arimo:wght@400;700&display=swap">
<style>
  :root {
    --navy: #1d3f6e;
    --steel: #3d6591;
    --red: #c8202f;
    --ink: #333a42;
    --grey: #6c7480;
    --paper: #ffffff;
    --backdrop: #e9e7e3;
    --soft-blue: #dfe7f1;
  }
  * { margin: 0; padding: 0; box-sizing: border-box; }
  html, body { width: 1200px; height: 950px; overflow: hidden; }
  body {
    background: var(--backdrop);
    font-family: "Arimo", Arial, sans-serif;
    color: var(--ink);
    position: relative;
  }
  .card {
    position: absolute;
    left: 250px;
    width: 700px;
    height: 400px;
    background: var(--paper);
    box-shadow: 0 6px 22px rgba(0,0,0,0.18);
  }
  .card--back { top: 50px; }
  .card--front { top: 500px; }

  .wordmark {
    font-weight: 700;
    color: var(--navy);
    letter-spacing: 0.06em;
    white-space: nowrap;
    display: flex;
    align-items: center;
    gap: 14px;
  }
  .wordmark__dot {
    width: 22px; height: 22px;
    border-radius: 50%;
    background: var(--red);
    flex: none;
  }
  .tagline {
    font-size: 11px;
    letter-spacing: 0.12em;
    text-transform: uppercase;
    color: var(--grey);
    border-top: 1px solid var(--red);
    padding-top: 4px;
    margin-top: 6px;
  }

  /* back side */
  .back__lockup {
    position: absolute;
    left: 50%; top: 150px;
    transform: translateX(-50%);
    text-align: center;
  }
  .back__lockup .wordmark { font-size: 30px; }
  .back__site {
    position: absolute;
    right: 90px; bottom: 40px;
    font-size: 17px;
    letter-spacing: 0.2em;
    color: var(--grey);
  }

  /* front side */
  .front__lockup { position: absolute; left: 40px; top: 34px; }
  .front__lockup .wordmark { font-size: 24px; }
  .front__lockup .wordmark__dot { width: 18px; height: 18px; }
  .person { position: absolute; left: 40px; top: 118px; }
  .person__name { font-size: 20px; color: var(--navy); letter-spacing: 0.03em; }
  .person__title { font-size: 15px; color: var(--red); letter-spacing: 0.04em; margin-top: 2px; }
  .contact { position: absolute; left: 40px; top: 178px; font-size: 15.5px; line-height: 23px; }
  .contact__address { padding-left: 22px; }
  .contact__list { list-style: none; }
  .contact__list li { display: flex; align-items: center; gap: 8px; }
  .contact__list svg { width: 14px; height: 14px; fill: var(--navy); flex: none; }
  .front__emblem {
    position: absolute;
    right: 70px; top: 70px;
    width: 260px; height: 260px;
    border-radius: 50%;
    background: var(--soft-blue);
  }
</style>
</head>
<body>
  <section class="card card--back" aria-label="Business card, back">
    <div class="back__lockup">
      <div class="wordmark"><span class="wordmark__dot"></span>BRELLWICK PARTNERS, LLC</div>
      <div class="tagline">Financial Planning and Consulting</div>
    </div>
    <div class="back__site">www.brellwickpartners.com</div>
  </section>

  <section class="card card--front" aria-label="Business card, front">
    <div class="front__lockup">
      <div class="wordmark"><span class="wordmark__dot"></span>BRELLWICK PARTNERS, LLC</div>
      <div class="tagline">Financial Planning and Consulting</div>
    </div>
    <div class="person">
      <div class="person__name">DANIEL ROE</div>
      <div class="person__title">PRESIDENT</div>
    </div>
    <div class="contact">
      <div class="contact__address">2716 Harwell Lane<br>Linden Grove, NY 11020</div>
      <ul class="contact__list">
        <li><svg viewBox="0 0 16 16"><path d="M3 1h3l1.5 4-2 1.3a9 9 0 0 0 4.2 4.2L11 8.5l4 1.5v3c0 1-1 2-2 2C6.5 15 1 9.5 1 3c0-1 1-2 2-2z"/></svg>555 0142 7731</li>
        <li><svg viewBox="0 0 16 16"><path d="M4 1h8v4H4zM1 6h14v7h-3v2H4v-2H1zM5 11v3h6v-3z"/></svg>555 0198 4420</li>
        <li><svg viewBox="0 0 16 16"><path d="M1 3h14v10H1zM2 4.5v.6l6 4 6-4v-.6z"/></svg>daniel@brellwick.com</li>
        <li><svg viewBox="0 0 16 16"><path d="M8 1a7 7 0 1 0 0 14A7 7 0 0 0 8 1zm0 2a5 5 0 0 1 4.9 4H3.1A5 5 0 0 1 8 3zM3.1 9h9.8A5 5 0 0 1 3.1 9z"/></svg>www.brellwickpartners.com</li>
      </ul>
    </div>
    <div class="front__emblem"></div>
  </section>
</body>
</html>
```